Packaging design for a reclosable bag for our product

We have a logo, and we need to put it on packaging for our product and while we want the look to be simple, we want it to follow good design principles and also contain spaces for other product descriptions.

There will be 5 sizes at launch so I'd like 5 variations, one for each size.

I've included a few mockups of the type of bag that I made but they are all just rough ideas that I had.

I want the brand to look scientific and methodical and even a bit quirky, as in "wow this is a serious product but also a bit unusual."

```html
<!DOCTYPE html>
<html lang="en">
<head>
<meta charset="UTF-8">
<title>VOLTA Bias Lighting – XL Pouch</title>
<link href="https://fonts.googleapis.com/css2?family=Nunito+Sans:wght@400;800;900&display=swap" rel="stylesheet">
<style>
  :root {
    --page: #ffffff;
    --pouch: #1f1f1f;
    --pouch-edge: #191919;
    --strip: #2b2b2b;
    --band: #141414;
    --zip: #111111;
    --accent: #1a8ce0;
    --ink: #f2f2f2;
  }
  * { margin: 0; padding: 0; box-sizing: border-box; }
  html, body {
    width: 1200px; height: 1200px; overflow: hidden;
    background: var(--page);
    font-family: "Nunito Sans", sans-serif;
  }
  .canvas { position: relative; width: 1200px; height: 1200px; }

  .pouch {
    position: absolute; left: 270px; top: 100px;
    width: 660px; height: 1000px;
    background: var(--pouch);
    border-radius: 26px 26px 6px 6px;
    overflow: hidden;
  }
  .pouch__strip {
    position: absolute; left: 0; top: 0;
    width: 110px; height: 100%;
    background: var(--strip);
  }
  .pouch__zip {
    position: absolute; left: 0; width: 100%;
    height: 6px; background: var(--zip);
  }
  .pouch__zip--upper { top: 98px; }
  .pouch__zip--lower { top: 128px; height: 10px; }

  .size-length {
    position: absolute; left: 55px; top: 603px;
    transform-origin: 0 0; transform: rotate(-90deg);
    color: var(--accent);
    font-size: 44px; font-weight: 400; white-space: nowrap;
    line-height: 1;
  }
  .size-length__num { font-weight: 900; font-size: 50px; margin-right: 6px; }

  .size-band {
    position: absolute; left: 0; top: 630px;
    width: 110px; height: 152px; background: var(--band);
  }
  .size-badge {
    position: absolute; left: 0; top: 655px;
    width: 110px; height: 105px; background: var(--accent);
  }
  .size-badge__text {
    position: absolute; left: 50%; top: 50%;
    transform: translate(-50%, -50%) rotate(-90deg);
    color: #fff; font-weight: 900; font-size: 52px; line-height: 1;
  }

  .brand {
    position: absolute; left: 130px; top: 530px;
    color: #ffffff; font-weight: 900; font-size: 96px;
    line-height: 1; letter-spacing: -2px;
  }
  .product-name {
    position: absolute; left: 132px; top: 668px;
    color: var(--ink); font-size: 46px; font-weight: 400; line-height: 1.1;
    letter-spacing: 0.5px;
  }
  .product-size {
    position: absolute; left: 132px; top: 722px;
    color: var(--ink); font-size: 28px; line-height: 1.1;
  }
  .spec {
    position: absolute; left: 132px; top: 790px;
    color: var(--ink); font-size: 30px; line-height: 1.25;
    letter-spacing: 0.3px;
  }
</style>
</head>
<body>
<div class="canvas">
  <div class="pouch">
    <div class="pouch__strip"></div>
    <div class="pouch__zip pouch__zip--upper"></div>
    <div class="pouch__zip pouch__zip--lower"></div>

    <div class="size-band"></div>
    <div class="size-length"><span class="size-length__num">5</span>meters</div>
    <div class="size-badge"><span class="size-badge__text">XL</span></div>

    <div class="brand">VOLTA</div>
    <div class="product-name">Bias Lighting</div>
    <div class="product-size">Extra large</div>
    <div class="spec">Simulated D65 CRI 90+<br>6500K White Bias Lighting</div>
  </div>
</div>
</body>
</html>
```